Hollow Thicket, a 3d voxel survival video game needs a card for gaming conventions

I am the lead developer for Hollow Thicket http://www.HollowThicket.example and need a business card to hand out at an indie gaming convention
The card would need to include the game name, website url, my name, position (Lead Developer), e-mail and phone number
The game is a 3d, voxel (with smooth terrain) based survival game with guns and wildlife. The main icon of the game would likely be a grizzly bear but I am willing to accept other designs too.
Attached is a media kit for the game with some images you can use but don't have to its just what little art I can provide. Anything on the website or from the video game can also be used. unrelated art can also be used.
Target Market(s)
Indie Developers/publishers at conferences
Industry/Entity Type
Games
Contact Information for Business Card
Name: Corin Waldrick
Position: Lead Developer
E-mail: Pale_Kettle@mailbox.example
Phone number: 555-372-1186

```html
<!DOCTYPE html>
<html lang="en">
<head>
<meta charset="utf-8">
<title>Hollow Thicket – Business Card</title>
<link href="https://fonts.googleapis.com/css2?family=Open+Sans:wght@400;600;700&display=swap" rel="stylesheet">
<style>
  :root {
    --stage: #e7e3de;
    --card-top: #b39d5e;
    --card-mid: #a9552c;
    --card-bottom: #a3150e;
    --fur-light: #8a6a47;
    --fur-dark: #3f2c1c;
    --title-red: #7c1410;
    --ink-light: #ffffff;
  }
  * { box-sizing: border-box; margin: 0; padding: 0; }
  html, body { width: 1200px; height: 900px; overflow: hidden; }
  body {
    background: var(--stage);
    font-family: "Open Sans", Arial, sans-serif;
    position: relative;
  }
  .card {
    position: absolute;
    overflow: hidden;
    background: linear-gradient(180deg, var(--card-top) 0%, var(--card-mid) 55%, var(--card-bottom) 100%);
    box-shadow: 0 6px 18px rgba(0,0,0,0.25);
  }
  .card--front { left: 238px; top: 62px; width: 555px; height: 341px; }
  .card--back  { left: 459px; top: 518px; width: 559px; height: 342px; }

  .bear-art { position: absolute; inset: 0; width: 100%; height: 100%; }

  .game-name {
    position: absolute;
    color: var(--title-red);
    font-weight: 700;
    text-transform: uppercase;
    letter-spacing: 1px;
    white-space: nowrap;
  }
  .card--front .game-name { left: 24px; top: 24px; font-size: 29px; line-height: 1.2; }
  .card--back .game-name {
    left: 266px; top: 130px; width: 300px;
    font-size: 42px; line-height: 1.05;
    text-align: center;
    transform: rotate(60deg);
    transform-origin: center;
  }

  .contact { position: absolute; left: 22px; top: 92px; color: var(--ink-light); }
  .contact__name { font-size: 17px; font-weight: 600; line-height: 1.3; }
  .contact__role { font-size: 14px; line-height: 1.3; }
  .contact__list { list-style: none; margin-top: 18px; font-size: 14px; }
  .contact__list li { display: flex; align-items: center; gap: 9px; height: 20px; }
  .contact__list svg { width: 11px; height: 11px; flex: none; }
  .icon-fill { fill: var(--ink-light); }
  .icon-line { fill: none; stroke: var(--ink-light); stroke-width: 2.2; }
</style>
</head>
<body>
  <section class="card card--front">
    <svg class="bear-art" viewBox="0 0 555 341" role="img" aria-label="Roaring grizzly bear photograph, head raised to the right">
      <defs>
        <linearGradient id="furFront" x1="0" y1="0" x2="1" y2="1">
          <stop offset="0" stop-color="#8a6a47"/>
          <stop offset="1" stop-color="#3f2c1c"/>
        </linearGradient>
      </defs>
      <path d="M130 341 C190 290 240 230 268 150 C280 110 300 80 340 62 C400 40 460 15 500 0 L555 0 L555 341 Z" fill="url(#furFront)"/>
    </svg>
    <h1 class="game-name">Hollow Thicket</h1>
    <div class="contact">
      <p class="contact__name">Corin Waldrick</p>
      <p class="contact__role">Lead Developer</p>
      <ul class="contact__list">
        <li><svg viewBox="0 0 24 24"><path class="icon-fill" d="M6.6 10.8a15.1 15.1 0 0 0 6.6 6.6l2.2-2.2a1 1 0 0 1 1-.25 11.4 11.4 0 0 0 3.6.57 1 1 0 0 1 1 1V20a1 1 0 0 1-1 1A17 17 0 0 1 3 4a1 1 0 0 1 1-1h3.5a1 1 0 0 1 1 1c0 1.25.2 2.45.57 3.57a1 1 0 0 1-.25 1z"/></svg>555-372-1186</li>
        <li><svg viewBox="0 0 24 24"><path class="icon-fill" fill-rule="evenodd" d="M2 4h20v16H2zM4 6v.5l8 6 8-6V6z"/></svg>Pale_Kettle@mailbox.example</li>
        <li><svg viewBox="0 0 24 24"><circle class="icon-line" cx="12" cy="12" r="9.5"/><path class="icon-line" d="M2.5 12h19M12 2.5c3 3 3 16 0 19M12 2.5c-3 3-3 16 0 19"/></svg>www.HollowThicket.example</li>
      </ul>
    </div>
  </section>

  <section class="card card--back">
    <svg class="bear-art" viewBox="0 0 559 342" role="img" aria-label="Roaring grizzly bear photograph, head raised to the left">
      <defs>
        <linearGradient id="furBack" x1="1" y1="0" x2="0" y2="1">
          <stop offset="0" stop-color="#8a6a47"/>
          <stop offset="1" stop-color="#3f2c1c"/>
        </linearGradient>
      </defs>
      <path d="M0 0 L70 0 C140 30 210 70 250 120 C280 170 300 230 330 270 C360 310 400 330 425 342 L0 342 Z" fill="url(#furBack)"/>
    </svg>
    <p class="game-name">Hollow<br>Thicket</p>
  </section>
</body>
</html>
```